Bran-well Tide Gate Custom Brokers Limited

Name: Lorvina Hadcott
Title: Customs Broker
Address: Shop 9 Ferncliff Commercial Complex
207-209 Mulgrave Road
Kingston 8
Telephone: (876)
Email: tidegatewell@mailbrook.example

```html
<!DOCTYPE html>
<html lang="en">
<head>
<meta charset="utf-8">
<title>Bran-well Tide Gate Custom Brokers Limited – Business Card</title>
<link rel="stylesheet" href="https://fonts.googleapis.com/css2?family=Poppins:wght@400;500;700;800&display=swap">
<style>
  :root {
    --navy: #0b2d55;
    --gold: #eaa912;
    --white: #ffffff;
    --page: #e9eaec;
    --ink: #0b2d55;
  }
  * { box-sizing: border-box; margin: 0; padding: 0; }
  html, body {
    width: 1200px;
    height: 1200px;
    overflow: hidden;
    background: var(--page);
    font-family: "Poppins", Arial, sans-serif;
  }
  .sheet {
    width: 1200px;
    height: 1200px;
    display: flex;
    flex-direction: column;
    align-items: center;
    justify-content: center;
    gap: 60px;
  }
  .card {
    width: 880px;
    height: 503px;
    position: relative;
    box-shadow: 0 10px 30px rgba(0,0,0,0.18);
  }
  .card--front {
    background: var(--navy);
    display: flex;
    align-items: center;
    justify-content: center;
  }
  .card--back {
    background: var(--white);
    display: flex;
    align-items: center;
  }
  .brand {
    display: flex;
    align-items: center;
    gap: 18px;
  }
  .brand__dot {
    width: 30px;
    height: 30px;
    border-radius: 50%;
    background: var(--gold);
    flex: none;
  }
  .brand__name {
    font-weight: 700;
    font-size: 34px;
    line-height: 1.2;
    color: var(--white);
  }
  .card--back .brand {
    width: 430px;
    justify-content: center;
  }
  .card--back .brand__name {
    color: var(--ink);
    font-size: 26px;
  }
  .divider {
    width: 2px;
    height: 270px;
    background: var(--navy);
    flex: none;
  }
  .contact {
    padding-left: 44px;
    color: var(--ink);
  }
  .contact__name {
    font-weight: 800;
    font-size: 32px;
    letter-spacing: 0.5px;
    line-height: 1.1;
  }
  .contact__title {
    font-weight: 500;
    font-size: 24px;
    color: var(--gold);
    margin-bottom: 18px;
  }
  .contact__address {
    font-style: normal;
    font-weight: 500;
    font-size: 21px;
    line-height: 1.3;
    margin-bottom: 16px;
  }
  .contact__row {
    display: flex;
    align-items: center;
    gap: 14px;
    font-size: 21px;
    font-weight: 500;
    line-height: 1.5;
  }
  .contact__icon {
    width: 26px;
    height: 26px;
    flex: none;
  }
</style>
</head>
<body>
  <main class="sheet">
    <section class="card card--front" aria-label="Card front">
      <div class="brand">
        <span class="brand__dot"></span>
        <span class="brand__name">Bran-well Tide Gate<br>Custom Brokers Limited</span>
      </div>
    </section>

    <section class="card card--back" aria-label="Card back">
      <div class="brand">
        <span class="brand__dot"></span>
        <span class="brand__name">Bran-well Tide Gate<br>Custom Brokers Limited</span>
      </div>
      <div class="divider"></div>
      <div class="contact">
        <h1 class="contact__name">LORVINA HADCOTT</h1>
        <p class="contact__title">Customs Broker</p>
        <address class="contact__address">
          Shop 9 Ferncliff<br>
          Commercial Complex<br>
          207-209 Mulgrave Road,<br>
          Kingston 8
        </address>
        <p class="contact__row">
          <svg class="contact__icon" viewBox="0 0 26 26" aria-hidden="true">
            <circle cx="13" cy="13" r="13" fill="#eaa912"/>
            <rect x="8.5" y="6.5" width="9" height="13" rx="1.5" fill="none" stroke="#fff" stroke-width="1.8"/>
          </svg>
          (876) 555 014 2290
        </p>
        <p class="contact__row">
          <svg class="contact__icon" viewBox="0 0 26 26" aria-hidden="true">
            <circle cx="13" cy="13" r="13" fill="#eaa912"/>
            <rect x="6.5" y="8.5" width="13" height="9" rx="1" fill="none" stroke="#fff" stroke-width="1.6"/>
            <path d="M6.8 9 L13 14 L19.2 9" fill="none" stroke="#fff" stroke-width="1.6"/>
          </svg>
          tidegatewell@mailbrook.example
        </p>
      </div>
    </section>
  </main>
</body>
</html>
```